BUSINESS CARD DESIGN

NAME- DALE VORSKIN
PHONE NUMER - 555- 714-9082
EMAIL- OFFICE@TRV-GROUNDMAKRZ.COM
BACK OF CARD- SPEACIALIZES IN LAND CLEARING, FORESTRY MUCLHING AND EXCAVATION

Contact Information for Business Card

NAME- DALE VORSKIN PHONE NUMER - 555- 714-9082 EMAIL- OFFICE@TRV-GROUNDMAKRZ.COM BACK OF CARD- SPEACIALIZES IN LAND CLEARING , MUCLHING AND EXCAVATION

```html
<!DOCTYPE html>
<html lang="en">
<head>
<meta charset="utf-8">
<title>Traverse Groundmakrz Business Card</title>
<link href="https://fonts.googleapis.com/css2?family=Audiowide&family=Poppins:wght@400;500&display=swap" rel="stylesheet">
<style>
  :root {
    --stage: #2b2b2b;
    --card-dark: #121212;
    --card-light: #f4f4f4;
    --ink-dark: #111111;
    --ink-light: #e9e9e9;
    --silver: #bfbfbf;
    --rule-dark: #5a5a5a;
    --rule-light: #8a8a8a;
  }
  * { box-sizing: border-box; margin: 0; padding: 0; }
  html, body { width: 1200px; height: 689px; overflow: hidden; }
  body {
    background: var(--stage);
    display: flex;
    align-items: center;
    justify-content: center;
    gap: 40px;
    font-family: "Poppins", sans-serif;
  }
  .card {
    width: 550px;
    height: 314px;
    border-radius: 18px;
    position: relative;
    overflow: hidden;
  }
  .card-back {
    background: linear-gradient(160deg, #1c1c1c, var(--card-dark));
    color: var(--ink-light);
    display: flex;
    flex-direction: column;
    align-items: center;
    padding-top: 40px;
  }
  .brand {
    display: flex;
    flex-direction: column;
    align-items: center;
    gap: 10px;
  }
  .brand-mark {
    width: 70px; height: 70px;
    border-radius: 50%;
    background: var(--silver);
  }
  .brand-name {
    font-family: "Audiowide", sans-serif;
    font-size: 19px;
    letter-spacing: 1px;
    text-align: center;
    line-height: 1.25;
  }
  .card-back .brand-name { color: var(--silver); }
  .card-back .brand-phone {
    font-family: "Audiowide", sans-serif;
    font-size: 13px;
    letter-spacing: 5px;
    color: #6d6d6d;
    border-top: 1px solid var(--rule-dark);
    padding-top: 4px;
  }
  .specialties-title {
    font-family: "Audiowide", sans-serif;
    font-size: 20px;
    margin-top: 22px;
    letter-spacing: 1px;
  }
  .specialties {
    list-style: none;
    display: flex;
    gap: 14px;
    margin-top: 12px;
    font-size: 15px;
    letter-spacing: 0.5px;
  }
  .specialties li { display: flex; align-items: center; gap: 7px; }
  .specialties li::before {
    content: "";
    width: 6px; height: 6px;
    background: var(--silver);
    transform: rotate(45deg);
  }
  .card-front {
    background: var(--card-light);
    color: var(--ink-dark);
    display: flex;
    align-items: center;
    padding: 0 36px 0 34px;
  }
  .card-front .brand { width: 200px; }
  .card-front .brand-mark { background: var(--ink-dark); }
  .card-front .brand-name { color: var(--ink-dark); font-size: 16px; }
  .contact { margin-left: 40px; flex: 1; }
  .person-name {
    font-family: "Audiowide", sans-serif;
    font-size: 26px;
    letter-spacing: 0.5px;
    padding-bottom: 12px;
    border-bottom: 1px solid var(--rule-light);
  }
  .contact-list { list-style: none; margin-top: 18px; display: grid; gap: 12px; }
  .contact-list li { display: flex; align-items: center; gap: 10px; font-size: 15px; }
  .icon {
    width: 26px; height: 26px; border-radius: 50%;
    background: var(--ink-dark);
    display: flex; align-items: center; justify-content: center;
    flex: none;
  }
  .icon svg { width: 14px; height: 14px; }
</style>
</head>
<body>
  <section class="card card-back">
    <div class="brand">
      <div class="brand-mark"></div>
      <div class="brand-name">TRAVERSE GROUNDMAKRZ LLC</div>
      <div class="brand-phone">555-714-9082</div>
    </div>
    <h2 class="specialties-title">SPECIALIZES IN</h2>
    <ul class="specialties">
      <li>LAND CLEARING</li>
      <li>MULCHING</li>
      <li>EXCAVATION</li>
    </ul>
  </section>

  <section class="card card-front">
    <div class="brand">
      <div class="brand-mark"></div>
      <div class="brand-name">TRAVERSE GROUNDMAKRZ LLC</div>
    </div>
    <div class="contact">
      <h1 class="person-name">DALE VORSKIN</h1>
      <ul class="contact-list">
        <li>
          <span class="icon"><svg viewBox="0 0 24 24" fill="#fff"><path d="M6.6 10.8a15 15 0 0 0 6.6 6.6l2.2-2.2a1 1 0 0 1 1-.25 11.4 11.4 0 0 0 3.6.57 1 1 0 0 1 1 1V20a1 1 0 0 1-1 1A17 17 0 0 1 3 4a1 1 0 0 1 1-1h3.5a1 1 0 0 1 1 1c0 1.25.2 2.45.57 3.57a1 1 0 0 1-.25 1z"/></svg></span>
          555- 714-9082
        </li>
        <li>
          <span class="icon"><svg viewBox="0 0 24 24" fill="none" stroke="#fff" stroke-width="2"><rect x="3" y="5" width="18" height="14" rx="1"/><path d="M3 6l9 7 9-7"/></svg></span>
          office@trv-groundmakrz.com
        </li>
        <li>
          <span class="icon"><svg viewBox="0 0 24 24" fill="none" stroke="#fff" stroke-width="2"><circle cx="12" cy="12" r="9"/><path d="M3 12h18M12 3c3 3 3 15 0 18M12 3c-3 3-3 15 0 18"/></svg></span>
          www.trv-groundmakrz.com
        </li>
      </ul>
    </div>
  </section>
</body>
</html>
```